Golf Brochure + Business Card Design Project – Kestrel Fitness.

Task Description

We are looking for a premium tri-fold brochure (8.5x11 letter, folded) plus a new business card design for Kestrel Fitness. Both need to look polished, elegant, and professional — something that would feel at home in a golf club environment.

Brochure Scope:
• Tri-fold brochure promoting our new golf-specific services
• Incorporate brand colors: deep hunter green, cream, and gold accents
• Clean, modern typography (professional, not playful)
• Layout will follow the copy provided (final copy attached, no rewriting needed)
• Imagery: mature golfers (50+), golf lifestyle shots, no generic stocky images
• Include QR code placement linking to booking page
• Deliverables: print-ready PDF with bleed/crop (CMYK), high-res PDF (digital), and source file (InDesign or Illustrator)

Business Card Scope:
• Front + back design
• Consistent with brand colors and fonts
• Space for name, title, phone, email, and website
• Deliverables: print-ready PDF with bleed/crop (CMYK) + source file (AI or InDesign)
• If possible, provide editable template for future staff cards

Timeline:
• First draft within 5–7 days
• 2 rounds of revisions included

Budget:
$300 USD (total for both brochure + business card)

I’ll provide finalized copy if you accept the project.
Project description (paste this whole block in that box)

We need a premium tri-fold brochure (8.5”×11” letter, folded) and a new business card design for Kestrel Fitness. This will be presented to golf course managers and members, so the look must be elegant, restrained, and country-club-classy.

Scope — Brochure
• Format: Tri-fold, 8.5”×11”. Please set 0.125” bleed on all sides and keep critical text ≥0.125–0.25” inside the trim.
• Purpose: Promote Kestrel Fitness’ golf-specific services for adults 50+.
• Copy: We will provide finalized copy in a Word doc after acceptance. No rewriting needed — please focus on layout and polish.
• Imagery (required):
• Golf-first images (ball on tee/green, mature golfers mid-swing, and golf course landscapes at golden hour).
• 1–2 real Kestrel Fitness gym photos on inside panels (trainer with client doing golf-relevant movement: stretch, rotation, balance).
• Visual style: Premium, quiet, lots of white/negative space, balanced grids; no clutter.
• Brand colors (required): Hunter Green #0C2E1F, Gold #CBA135, Cream #F5F2EB. Convert for CMYK print while preserving the look.
• Typography: Clean, legible serif + sans pairing (e.g., modern serif for headlines, humanist/neo-grotesk sans for body). You may propose suitable professional fonts; avoid playful/novelty fonts.
• Elements to include:
• Our logo (we will upload).
• QR code placement to booking page (we will supply the URL / QR asset).
• Simple icon treatment for the three complimentary options (Strength & Mobility, Stretch Therapy, Vitrascan + Assessment).
• Deliverables:
• Print-ready PDF (CMYK, with bleed & crop marks, PDF/X-1a or PDF/X-4)
• High-res digital PDF (no bleed)
• Source file (InDesign or Illustrator) + packaged fonts/links or outlined type as appropriate.

Scope — Business Card
• Size: 3.5”×2” (US standard) with 0.125” bleed; keep text ≥0.125” from trim.
• Front/back design; consistent with brochure branding.
• Fields: Name, Title, Phone, Email, Website, Address; optional small QR on back.
• Deliverables: Print-ready PDF (CMYK, bleed & crops) + Source file (AI/INDD). Provide an editable template for staff names.

Process & Timing
• Initial concept for brochure + card within 5–7 days of acceptance.
• 2 rounds of revisions included.
• Please start with a clean layout concept using placeholder images/text blocks; we’ll drop in final copy/assets immediately after acceptance.

Stock & Licensing
• You may propose stock images that fit the brief (we’re fine approving Pixelgrove or equivalent). Please note any license fees separately if needed.

Usage Rights
• We require full usage rights to the final designs for print & digital.

Target Market(s)

Golfers 50+ in Victoria, BC: quality-oriented, health-conscious, want to play longer, stronger, and pain-free. Country-club aesthetic; expect polished, professional materials.

Industry/Entity Type

Health & Fitness — Golf Performance / Longevity Studio

Font styles to use
Serif
Sans Serif

Requirements
Must have
• • Golf-first imagery + 1–2 real Kestrel Fitness photos inside. • Brand colors: #0C2E1F (Hunter Green), #CBA135 (Gold), #F5F2EB (Cream). • Premium, restrained layout; ample negative space; no clutter. • Clean professional serif + sans type pairing; highly legible. • Space for logo and QR code (booking). • Correct print specs (bleed, crops, CMYK). • Deliverables: print-ready PDFs (brochure + card), digital PDF, source files.
Nice to have
• • Subtle texture or grain in backgrounds (very light) to add sophistication. • A second brochure cover variation (ball on tee vs. course landscape) at concept stage.
Should not have
• • Cheesy/posed “stocky” groups; overly young models; beer/alcohol imagery. • Over-saturated greens/blues; gimmicky gradients or clip art. • Generic fitness/bodybuilding shots unrelated to golf performance.

```html
<!DOCTYPE html>
<html lang="en">
<head>
<meta charset="utf-8">
<title>Kestrel Fitness – Exclusive Golf Invitation Brochure</title>
<link rel="stylesheet" href="https://fonts.googleapis.com/css2?family=Oswald:wght@500&family=Poppins:ital,wght@0,400;0,500;0,600;0,700;1,400&display=swap">
<style>
  :root {
    --green: #0e3a33;
    --green-deep: #0a2e28;
    --gold: #d4a91c;
    --gold-light: #f0d36a;
    --cream: #fbf7ea;
    --ink: #12332d;
    --backdrop: #6e6e6e;
  }
  * { margin: 0; padding: 0; box-sizing: border-box; }
  html, body { width: 1200px; height: 909px; overflow: hidden; }
  body { background: var(--backdrop); font-family: "Poppins", sans-serif; position: relative; }

  .spread {
    position: absolute; top: 227px;
    width: 884px; height: 684px;
    transform: scale(0.665); transform-origin: 0 0;
    overflow: hidden;
    box-shadow: 0 6px 18px rgba(0,0,0,.35);
  }
  .spread--outside { left: 8px; background: var(--green); }
  .spread--inside { left: 604px; background: var(--cream); }
  .shapes { position: absolute; inset: 0; }
  .abs { position: absolute; }

  .condensed { font-family: "Oswald", sans-serif; font-weight: 500; letter-spacing: -0.5px; line-height: 1; }

  /* Back panel */
  .about-tag { left: 0; top: 45px; width: 90px; height: 30px; background: var(--gold); color: var(--green-deep); font-size: 22px; padding: 3px 0 0 20px; }
  .about-title { left: 100px; top: 36px; color: var(--cream); font-size: 48px; }
  .about-intro { left: 100px; top: 96px; width: 300px; color: var(--cream); font-size: 14.5px; line-height: 21px; }
  .about-list { left: 100px; top: 148px; list-style: none; color: var(--cream); font-size: 14px; line-height: 21px; }
  .about-list li::before { content: "✓"; color: var(--gold); font-weight: 700; margin-right: 8px; }
  .coach-note { left: 48px; top: 253px; width: 336px; height: 47px; border: 2px solid var(--gold-light); border-radius: 6px; background: var(--cream); color: var(--ink); font-size: 13px; line-height: 16px; text-align: center; padding-top: 6px; }
  .contact { right: 474px; top: 553px; color: var(--cream); font-size: 12.5px; line-height: 19px; text-align: right; }
  .contact span::after { content: ""; display: inline-block; width: 7px; height: 7px; border-radius: 50%; background: var(--gold); margin-left: 6px; }
  .fine-print { left: 83px; top: 636px; color: var(--cream); font-size: 11px; }

  /* Brand marks */
  .brand-mark { position: absolute; display: flex; align-items: center; justify-content: center; text-align: center; border-radius: 50%; font-family: "Poppins", sans-serif; font-weight: 600; color: var(--green-deep); background: var(--cream); line-height: 1.15; }
  .brand-mark--small { left: 320px; top: 440px; width: 90px; height: 90px; font-size: 14px; }
  .brand-mark--cover { left: 645px; top: 197px; width: 130px; height: 130px; font-size: 20px; }

  /* Front cover */
  .cover-title { left: 476px; top: 38px; color: var(--cream); font-size: 47px; line-height: 47px; }
  .cover-invite { left: 442px; width: 442px; top: 443px; text-align: center; color: var(--cream); font-size: 21px; line-height: 27px; }
  .cover-club { left: 442px; width: 442px; top: 508px; text-align: center; color: var(--gold); font-size: 27px; font-weight: 500; }
  .cover-web { left: 442px; width: 442px; top: 612px; text-align: center; color: var(--cream); font-size: 14.5px; letter-spacing: .3px; }

  /* Inside pages: shared heading block */
  .page-kicker { width: 442px; text-align: center; font-size: 24px; top: 18px; }
  .page-headline { width: 442px; text-align: center; font-weight: 700; font-size: 30px; line-height: 34px; top: 40px; letter-spacing: .5px; }
  .page-lede { width: 442px; text-align: center; font-size: 11px; line-height: 14px; top: 82px; padding: 0 22px; letter-spacing: .2px; }
  .why { left: 0; }
  .gift { left: 442px; }
  .why.page-kicker, .why.page-lede { color: var(--cream); }
  .why.page-headline { color: var(--gold); }
  .gift.page-kicker, .gift.page-headline, .gift.page-lede { color: var(--ink); }

  .statement { left: 20px; top: 272px; color: var(--ink); font-size: 19px; line-height: 21px; letter-spacing: .4px; }
  .statement b { font-weight: 700; }
  .statement-rule { left: 20px; top: 412px; width: 145px; height: 2px; background: var(--green); }
  .intro-copy { left: 20px; top: 430px; width: 390px; color: var(--ink); font-size: 12.5px; line-height: 16px; letter-spacing: .3px; }

  .benefit { display: flex; gap: 12px; align-items: flex-start; color: var(--ink); font-size: 12px; line-height: 15px; letter-spacing: .3px; width: 200px; }
  .benefit p { padding-top: 2px; }
  .icon-dot { flex: none; width: 42px; height: 42px; border-radius: 50%; background: var(--green); border: 2px solid var(--gold); display: flex; align-items: center; justify-content: center; }
  .icon-dot svg { width: 22px; height: 22px; }

  .offers-band { left: 442px; top: 138px; width: 442px; height: 28px; background: var(--green); color: var(--cream); font-size: 22px; text-align: center; padding-top: 2px; letter-spacing: 1px; }
  .offers-lead { left: 442px; width: 442px; top: 178px; text-align: center; color: var(--ink); font-size: 12.5px; font-weight: 600; letter-spacing: .3px; }
  .offer { left: 472px; display: flex; gap: 12px; width: 400px; color: var(--ink); }
  .offer h3 { font-size: 13.5px; font-weight: 700; line-height: 16px; letter-spacing: .4px; }
  .offer p { font-size: 12.5px; line-height: 15px; letter-spacing: .3px; }

  .value { left: 480px; top: 484px; width: 100px; text-align: center; color: var(--ink); font-size: 10.5px; font-weight: 600; line-height: 12px; }
  .value-price { display: inline-block; background: var(--green); color: var(--cream); padding: 0 8px; font-size: 12.5px; line-height: 15px; margin-top: 1px; }
  .value-note { left: 472px; top: 520px; width: 130px; text-align: center; color: var(--ink); font-size: 9px; font-style: italic; line-height: 11px; }
  .redeem { left: 472px; top: 549px; width: 115px; height: 16px; background: var(--green); color: var(--cream); font-size: 12px; text-align: center; line-height: 16px; }
  .redeem-note { left: 472px; top: 570px; width: 160px; color: var(--ink); font-size: 9.5px; font-weight: 600; line-height: 11px; }
  .gift-web { left: 442px; width: 442px; top: 619px; text-align: center; color: var(--cream); font-size: 14.5px; letter-spacing: .5px; }
</style>
</head>
<body>

<section class="spread spread--outside" aria-label="Brochure outside: back panel and front cover">
  <svg class="shapes" viewBox="0 0 884 684">
    <defs>
      <linearGradient id="gold-line" x1="0" y1="0" x2="1" y2="1">
        <stop offset="0" stop-color="#f3d874"/><stop offset=".5" stop-color="#c9981a"/><stop offset="1" stop-color="#f0d36a"/>
      </linearGradient>
      <linearGradient id="studio" x1="0" y1="0" x2="1" y2="1">
        <stop offset="0" stop-color="#2c3c4a"/><stop offset=".55" stop-color="#6e6a55"/><stop offset="1" stop-color="#b79a66"/>
      </linearGradient>
      <linearGradient id="green-course" x1="0" y1="0" x2="1" y2="1">
        <stop offset="0" stop-color="#4f7a35"/><stop offset=".5" stop-color="#b9cf7a"/><stop offset="1" stop-color="#e7eec0"/>
      </linearGradient>
      <linearGradient id="gym-dark" x1="0" y1="0" x2="0" y2="1">
        <stop offset="0" stop-color="#0e3a33" stop-opacity="0"/><stop offset=".4" stop-color="#1d3a3f" stop-opacity=".8"/><stop offset="1" stop-color="#263d44"/>
      </linearGradient>
    </defs>
    <path d="M0,410 C120,420 230,390 292,372 C285,470 210,560 80,590 C50,595 20,595 0,592 Z" fill="url(#studio)" role="img" aria-label="Photo: private training studio interior with framed wall art"/>
    <path d="M0,390 C120,400 240,380 296,372 C292,480 210,580 60,598" fill="none" stroke="url(#gold-line)" stroke-width="7"/>
    <rect x="442" y="380" width="442" height="304" fill="url(#gym-dark)" role="img" aria-label="Photo: trainer coaching a client on gym equipment, darkened"/>
    <path d="M690,0 H884 V320 C820,350 720,345 650,300 C600,260 595,200 620,140 C640,90 665,40 690,0 Z" fill="url(#green-course)" role="img" aria-label="Photo: smiling mature golfer in green sweater holding a red flag on the putting green"/>
    <path d="M686,0 C640,70 595,160 610,230 C625,300 720,350 884,310" fill="none" stroke="url(#gold-line)" stroke-width="6"/>
  </svg>

  <div class="abs about-tag condensed">ABOUT</div>
  <h2 class="abs about-title condensed">KESTREL FITNESS</h2>
  <p class="abs about-intro">Located in Victoria, <b>Kestrel Fitness</b> is a private training studio specializing in:</p>
  <ul class="abs about-list">
    <li>Personal Training for adults 40+</li>
    <li>Golf-specific performance coaching</li>
    <li>Stretch therapy and athletic therapy</li>
    <li>Longevity &amp; strength training</li>
  </ul>
  <p class="abs coach-note">Every coach holds a degree in Sports Science —<br>ensuring safe, proven, results-driven programs.</p>

  <div class="brand-mark brand-mark--small">Kestrel<br>Fitness</div>
  <p class="abs contact">
    <span>250-555-0147</span><br>
    <span>hello@kestrelfitness.biz</span><br>
    <span>kestrelfitnessvictoria.com</span>
  </p>
  <p class="abs fine-print">This invitation is exclusive and non-transferable.</p>

  <h1 class="abs cover-title condensed">EXCLUSIVE<br>GOLF<br>INVITATION</h1>
  <div class="brand-mark brand-mark--cover">Kestrel<br>Fitness</div>
  <p class="abs cover-invite">An exclusive invitation for<br>select members of</p>
  <p class="abs cover-club">[Golf Club Name]</p>
  <p class="abs cover-web">www.kestrelfitness.biz</p>
</section>

<section class="spread spread--inside" aria-label="Brochure inside: why golfers choose us and member gift">
  <svg class="shapes" viewBox="0 0 884 684">
    <defs>
      <linearGradient id="gold-line-2" x1="0" y1="0" x2="1" y2="0">
        <stop offset="0" stop-color="#f3d874"/><stop offset=".5" stop-color="#c9981a"/><stop offset="1" stop-color="#f0d36a"/>
      </linearGradient>
      <linearGradient id="gym-floor" x1="0" y1="0" x2="1" y2="0">
        <stop offset="0" stop-color="#3c4448"/><stop offset=".5" stop-color="#6d6a66"/><stop offset="1" stop-color="#23282b"/>
      </linearGradient>
      <linearGradient id="climb" x1="0" y1="0" x2="1" y2="1">
        <stop offset="0" stop-color="#1e2022"/><stop offset=".6" stop-color="#5b5049"/><stop offset="1" stop-color="#a08066"/>
      </linearGradient>
      <linearGradient id="stretch" x1="0" y1="0" x2="1" y2="1">
        <stop offset="0" stop-color="#2f4a6a"/><stop offset=".6" stop-color="#4a5563"/><stop offset="1" stop-color="#c46a3a"/>
      </linearGradient>
    </defs>
    <rect x="0" y="0" width="442" height="150" fill="var(--green)"/>
    <path d="M0,140 H442 V232 C300,252 140,248 0,210 Z" fill="url(#gym-floor)" role="img" aria-label="Photo: studio training floor with treadmills and racks"/>
    <path d="M0,210 C140,248 300,252 442,232" fill="none" stroke="url(#gold-line-2)" stroke-width="5"/>
    <path d="M442,255 V405 C380,412 290,400 245,340 C225,310 212,280 205,255 Z" fill="url(#climb)" role="img" aria-label="Photo: woman training on a climbing bar"/>
    <path d="M190,250 C205,300 230,360 290,392 C340,412 400,410 442,404" fill="none" stroke="url(#gold-line-2)" stroke-width="5"/>
    <path d="M884,480 V684 H770 C700,650 650,570 622,500 C700,482 800,476 884,480 Z" fill="url(#stretch)" role="img" aria-label="Photo: trainer guiding a client through a golf stretch"/>
    <path d="M608,492 C640,570 700,640 780,666 C820,676 860,678 884,676" fill="none" stroke="url(#gold-line-2)" stroke-width="5"/>
    <path d="M884,400 C870,440 845,470 810,490" fill="none" stroke="url(#gold-line-2)" stroke-width="4"/>
    <rect x="442" y="612" width="442" height="32" fill="var(--green)"/>
  </svg>

  <p class="abs why page-kicker condensed">WHY GOLFERS 50+ CHOOSE</p>
  <h2 class="abs why page-headline">KESTREL FITNESS</h2>
  <p class="abs why page-lede">The game changes as we age. Distance fades, flexibility tightens, and recovery after 18 holes takes longer than it used to. But that doesn't mean your best golf is behind you.</p>

  <p class="abs statement"><b>This isn't<br>generic gym<br>training</b>— it's<br>science-based<br>coaching tailored<br>to golfers.</p>
  <div class="abs statement-rule"></div>
  <p class="abs intro-copy">At <b>Kestrel Fitness,</b> we specialize in helping golfers 50+ build the strength, mobility, and balance needed to:</p>

  <div class="abs benefit" style="left:20px;top:500px">
    <span class="icon-dot"><svg viewBox="0 0 22 22"><circle cx="11" cy="8" r="4" fill="none" stroke="#fbf7ea" stroke-width="1.6"/><path d="M11 12v6M6 19h10" stroke="#fbf7ea" stroke-width="1.6"/></svg></span>
    <p>Add yards off the tee with rotational strength training</p>
  </div>
  <div class="abs benefit" style="left:231px;top:500px">
    <span class="icon-dot"><svg viewBox="0 0 22 22"><path d="M5 4v14M17 4v14M8 11h6" stroke="#fbf7ea" stroke-width="1.6"/></svg></span>
    <p>Reduce back and joint pain with targeted stability work</p>
  </div>
  <div class="abs benefit" style="left:20px;top:590px">
    <span class="icon-dot"><svg viewBox="0 0 22 22"><path d="M5 19V9l6-5 6 5v10M9 19v-6h4v6" fill="none" stroke="#fbf7ea" stroke-width="1.6"/></svg></span>
    <p>Maintain a fluid swing with improved shoulder and hip mobility</p>
  </div>
  <div class="abs benefit" style="left:231px;top:590px">
    <span class="icon-dot"><svg viewBox="0 0 22 22"><circle cx="12" cy="4" r="2" fill="#fbf7ea"/><path d="M12 7l-2 6 3 3-1 4M10 13l-4 6M11 9l4 3" fill="none" stroke="#fbf7ea" stroke-width="1.6"/></svg></span>
    <p>Walk off the 18th green feeling strong, not sore</p>
  </div>

  <p class="abs gift page-kicker condensed">YOUR EXCLUSIVE</p>
  <h2 class="abs gift page-headline">MEMBER GIFT</h2>
  <p class="abs gift page-lede">As one of the club's most valued golfers, you've been hand-selected to receive a complimentary premium experience at Kestrel Fitness.</p>

  <div class="abs offers-band condensed">OFFERS</div>
  <p class="abs offers-lead">Choose one of the following golf-specific sessions:</p>

  <div class="abs offer" style="top:213px">
    <span class="icon-dot"><svg viewBox="0 0 22 22"><path d="M4 11h14M7 7v8M15 7v8" stroke="#fbf7ea" stroke-width="1.6"/></svg></span>
    <div><h3>Golf Strength &amp; Mobility Session</h3><p>Add rotational power for more distance and protect your back.</p></div>
  </div>
  <div class="abs offer" style="top:279px">
    <span class="icon-dot"><svg viewBox="0 0 22 22"><circle cx="11" cy="5" r="2" fill="#fbf7ea"/><path d="M11 8v6l-4 5M11 14l5 4M6 10h10" fill="none" stroke="#fbf7ea" stroke-width="1.6"/></svg></span>
    <div><h3>Golf Flexibility &amp; Stretch Therapy</h3><p>Unlock tight hips and shoulders to swing easier and play longer.</p></div>
  </div>
  <div class="abs offer" style="top:344px">
    <span class="icon-dot"><svg viewBox="0 0 22 22"><rect x="5" y="4" width="12" height="14" rx="2" fill="none" stroke="#fbf7ea" stroke-width="1.6"/><path d="M8 12h2l1-3 1 5 1-2h2" fill="none" stroke="#fbf7ea" stroke-width="1.4"/></svg></span>
    <div><h3>Vitrascan + Golf Wellness Assessment</h3><p>Identify muscle imbalances and posture issues holding your game back.</p></div>
  </div>
  <div class="abs offer" style="top:409px">
    <span class="icon-dot"><svg viewBox="0 0 22 22"><circle cx="11" cy="5" r="2" fill="#fbf7ea"/><path d="M11 8v7M7 19l4-4 4 4M5 10h12" fill="none" stroke="#fbf7ea" stroke-width="1.6"/></svg></span>
    <div><h3>Golf-Specific Personal Training Session</h3><p>One-on-one workout to boost club-head speed, balance, and confidence.</p></div>
  </div>

  <p class="abs value">VALUED AT<br><span class="value-price">$110–$125</span></p>
  <p class="abs value-note">Reserved exclusively for<br>select golf members.</p>
  <p class="abs redeem">To Redeem:</p>
  <p class="abs redeem-note">Contact Kestrel Fitness directly. This invitation is limited and not available to the public.</p>
  <p class="abs gift-web">www.kestrelfitness.biz</p>
</section>

</body>
</html>
```